New Modern floristry business design

Hi, we are a new business based in Sydney called "copper fern floristry"

With so many floristry's we need a good design that will set a great first impression.

A few descriptive words on how we envision copper fern floristry:

-dynamic design
-minimal colour (colour can be used to enhance the design)
-black white grey (can include gold,silver,metallic shadowing)
Strong "COPPER FERN" with a classy "FLORISTRY"
Bold with a touch of feminine

Copper Fern Floristry,
Delia Pruett,
Copperfernfloristry@mailvista.com.au

```html
<!DOCTYPE html>
<html lang="en">
<head>
<meta charset="utf-8">
<title>Copper Fern Floristry – Business Card</title>
<link rel="stylesheet" href="https://fonts.googleapis.com/css2?family=Berkshire+Swash&display=swap">
<style>
  :root {
    --page-bg: #3a3a3c;
    --card-black: #050505;
    --silver: #a9a9ab;
    --silver-soft: #8f8f92;
    --bloom-light: rgba(120, 120, 124, 0.55);
    --bloom-mid: rgba(70, 70, 74, 0.45);
    --bloom-fade: rgba(5, 5, 5, 0);
  }

  * { margin: 0; padding: 0; box-sizing: border-box; }

  html, body {
    width: 1200px;
    height: 800px;
    overflow: hidden;
    background: var(--page-bg);
  }

  .canvas {
    position: relative;
    width: 1200px;
    height: 800px;
    display: flex;
    justify-content: center;
    align-items: center;
    gap: 120px;
  }

  .card {
    position: relative;
    width: 320px;
    height: 560px;
    background: var(--card-black);
    overflow: hidden;
    box-shadow: 0 14px 30px rgba(0, 0, 0, 0.45);
  }

  .floral-cluster {
    position: absolute;
    border-radius: 50%;
    background:
      radial-gradient(circle at 35% 40%, var(--bloom-light) 0%, var(--bloom-mid) 35%, var(--bloom-fade) 70%);
  }

  .floral-cluster--top-left {
    top: -60px;
    left: -60px;
    width: 280px;
    height: 240px;
  }

  .floral-cluster--top-band {
    top: -70px;
    left: -40px;
    width: 400px;
    height: 200px;
  }

  .floral-cluster--bottom-right {
    bottom: -50px;
    right: -60px;
    width: 320px;
    height: 260px;
    background:
      radial-gradient(circle at 60% 55%, var(--bloom-light) 0%, var(--bloom-mid) 35%, var(--bloom-fade) 70%);
  }

  .brand {
    position: absolute;
    left: 0;
    right: 0;
    text-align: center;
    font-family: "Berkshire Swash", cursive;
    font-weight: 400;
    color: var(--silver);
    line-height: 1;
  }

  .brand__name {
    display: block;
    font-size: 44px;
  }

  .brand__trade {
    display: block;
    font-size: 30px;
    margin-top: 4px;
  }

  .card--contact .brand { top: 170px; }
  .card--logo .brand { top: 190px; }

  .contact {
    position: absolute;
    top: 330px;
    left: 0;
    right: 0;
    text-align: center;
    font-family: "Berkshire Swash", cursive;
    color: var(--silver);
  }

  .contact__name {
    font-size: 30px;
    line-height: 1.2;
  }

  .contact__email {
    margin-top: 10px;
    font-size: 11.5px;
    color: var(--silver-soft);
    white-space: nowrap;
  }
</style>
</head>
<body>
  <main class="canvas">
    <section class="card card--contact" aria-label="Business card front">
      <div class="floral-cluster floral-cluster--top-left" role="img" aria-label="Soft grey blossom illustration"></div>
      <div class="floral-cluster floral-cluster--bottom-right" role="img" aria-label="Soft grey blossom illustration"></div>
      <h1 class="brand">
        <span class="brand__name">Copper Fern</span>
        <span class="brand__trade">Floristry</span>
      </h1>
      <div class="contact">
        <p class="contact__name">Delia Pruett</p>
        <p class="contact__email">Email: Copperfernfloristry@mailvista.com.au</p>
      </div>
    </section>

    <section class="card card--logo" aria-label="Business card back">
      <div class="floral-cluster floral-cluster--top-band" role="img" aria-label="Soft grey blossom illustration"></div>
      <div class="floral-cluster floral-cluster--bottom-right" role="img" aria-label="Soft grey blossom illustration"></div>
      <h2 class="brand">
        <span class="brand__name">Copper Fern</span>
        <span class="brand__trade">Floristry</span>
      </h2>
    </section>
  </main>
</body>
</html>
```